Bramblewood Joinery Website

My client Bramblewood Joinery is looking for a redesign for a Word Press Website. Their current site is at www.bramblewoodjoinery.example They are a custom cabinet company, but also create bathroom, living room, bar and entertainment and bedroom cabinets too. They would like a design that emulates the master craftsman work they do yet a contemporary style.

Their current site was designed using Flash elements.

Target Market(s)

Home owners and builders of high end homes

Industry/Entity Type

Entertainment

Font styles to use
Serif
Decorative

Requirements
Must have
• Must show their work and logo using a contemporary style.
Nice to have
• Sliders that showcase their projects.

```html
<!DOCTYPE html>
<html lang="en">
<head>
<meta charset="utf-8">
<title>Bramblewood Joinery</title>
<link href="https://fonts.googleapis.com/css2?family=Arimo:ital,wght@0,400;0,700;1,400&family=Cabin:wght@400;500&family=Oswald:wght@600;700&display=swap" rel="stylesheet">
<style>
:root{
  --green:#3db33d;
  --ink:#222;
  --text:#444;
  --muted:#777;
  --band:#e8e8e8;
  --dark:#3a3a3a;
  --darker:#1c1c1c;
  --footer:#2f2f2f;
  --white:#fff;
}
*{margin:0;padding:0;box-sizing:border-box}
html,body{width:1200px;height:2282px;overflow:hidden}
body{position:relative;background:var(--white);font-family:"Arimo",Arial,sans-serif;color:var(--text)}
.abs{position:absolute}
.topline{left:0;top:0;width:1200px;height:5px;background:var(--green)}
.header{left:0;top:5px;width:1200px;height:119px;background:var(--white)}
.brand{left:158px;top:18px}
.brand-mark{width:90px;height:90px;border-radius:50%;border:4px solid var(--green);display:flex;align-items:center;justify-content:center;text-align:center;font-family:"Cabin",sans-serif;font-size:13px;font-weight:500;color:var(--green);line-height:1.15}
.social-badge{left:736px;top:42px;width:141px;height:46px;border:1px solid #bbb;background:#f4f4f4;display:flex;align-items:center;gap:8px;padding-left:8px;font-size:17px;color:#2b4a8a}
.social-badge .sq{width:28px;height:28px;background:#2b4a8a}
.question{left:900px;top:40px;font-size:12px;color:var(--ink)}
.phone{left:900px;top:56px;font-weight:700;font-size:27px;color:var(--green);letter-spacing:1px}
.band{left:0;top:124px;width:1200px;height:412px;background:var(--band)}
.nav{left:162px;top:152px;width:878px;height:42px;background:var(--darker);display:flex;align-items:center}
.nav a{flex:none;white-space:nowrap;color:var(--white);text-decoration:none;font-size:10.5px;font-weight:700;padding:0 9px;height:42px;line-height:42px;border-right:1px solid #333;text-transform:uppercase}
.nav a.active{background:var(--green)}
.nav .search{margin-left:auto;flex:none;width:42px;height:42px;background:var(--green);display:flex;align-items:center;justify-content:center}
.slider{left:162px;top:205px;width:878px;height:394px;background:linear-gradient(160deg,#6b3a1c 0%,#a0602c 35%,#c98a4a 55%,#5a2e14 100%)}
.slide-title{left:162px;top:452px;width:878px;text-align:center;font-family:"Oswald",sans-serif;font-weight:700;font-size:40px;color:var(--white);letter-spacing:.5px}
.slide-sub{left:162px;top:505px;width:878px;text-align:center;font-size:19px;color:var(--white)}
.slide-arrow{top:387px;width:46px;height:46px;border:3px solid rgba(255,255,255,.8);border-radius:50%;display:flex;align-items:center;justify-content:center}
.dots{left:543px;top:556px;display:flex;gap:5px}
.dots i{width:13px;height:13px;border-radius:50%;background:#ddd;display:block}
.dots i.on{background:var(--green)}
.intro{left:0;top:626px;width:1200px;text-align:center;font-size:28px;line-height:1.25;color:var(--ink)}
.intro em{font-style:normal;color:var(--green)}
.offer{left:0;top:728px;width:1200px;height:301px;background:var(--dark)}
.section-title{font-family:"Cabin",sans-serif;font-size:23px;color:var(--ink);text-transform:uppercase;white-space:nowrap}
.offer-item{top:820px;width:150px;text-align:center;font-size:17px;color:var(--white);text-transform:uppercase;white-space:nowrap}
.offer-item svg{display:block;margin:0 auto 8px}
.offer-item.on{color:var(--green)}
.offer-text{left:170px;top:918px;width:860px;text-align:center;font-size:14.5px;line-height:1.55;color:#ddd}
.thumb{background:linear-gradient(150deg,#d9d4cc,#8d8276 60%,#3a3530)}
.thumb.dark{background:linear-gradient(150deg,#777,#2c2620 60%,#111)}
.thumb.light{background:linear-gradient(150deg,#f2efe9,#bdb3a6 60%,#6e6257)}
.btn{height:31px;line-height:31px;text-align:center;color:var(--white);font-size:13px;text-transform:uppercase}
.btn.dark{background:#1f2433}
.btn.green{background:var(--green)}
.news-item{left:787px;width:253px;height:72px;border-bottom:1px solid #ddd;display:flex;gap:10px}
.news-item .nt{width:52px;height:46px;flex:none}
.news-item h4{font-family:"Cabin",sans-serif;font-size:14px;font-weight:500;color:var(--ink);margin-bottom:3px;white-space:nowrap}
.news-item h4.hot{color:var(--green)}
.news-item p{font-size:11.5px;line-height:1.35;color:var(--muted)}
.rule{left:162px;top:1430px;width:878px;height:1px;background:#ddd}
.avatar{left:162px;top:1508px;width:70px;height:67px;background:linear-gradient(160deg,#c89a7c,#6d4a38)}
.bubble{left:249px;top:1508px;width:327px;height:134px;background:var(--green);border-radius:6px;padding:11px 14px;font-style:italic;font-size:10.5px;line-height:1.45;color:var(--white);text-align:justify;overflow:hidden}
.bubble:before{content:"";position:absolute;left:-12px;top:18px;border:8px solid transparent;border-right:12px solid var(--green);border-left:0}
.quote-by{left:262px;top:1650px;font-style:italic;font-size:13px;color:var(--text)}
.client{font-family:"Cabin",sans-serif;font-size:30px;font-weight:500;color:#111;text-align:center;width:140px;white-space:nowrap}
.hello{left:0;top:1706px;width:1200px;height:253px;background:var(--band)}
.hello-title{left:0;top:1762px;width:1200px;text-align:center;font-family:"Oswald",sans-serif;font-weight:700;font-size:33px;color:var(--ink)}
.hello-text{left:175px;top:1816px;width:850px;text-align:center;font-size:13.5px;line-height:1.5;color:var(--muted)}
.socials{left:513px;top:1866px;display:flex;gap:16px}
.socials span{width:36px;height:36px;border-radius:50%;display:flex;align-items:center;justify-content:center;color:var(--white);font-size:9px;font-weight:700}
.footer{left:0;top:1959px;width:1200px;height:285px;background:var(--footer)}
.footer-title{top:2006px;font-family:"Cabin",sans-serif;font-size:17px;font-weight:400;color:var(--white);text-transform:uppercase}
.footer-about{left:162px;top:2040px;width:270px;font-size:11.5px;line-height:1.9;color:#ddd;text-align:justify}
.footer-about b{color:var(--white)}
.pf{width:53px;height:42px}
.contact{left:789px;top:2040px;width:260px;font-size:11px;line-height:1.55;color:#ddd}
.contact b{color:var(--white)}
.contact-row{display:flex;align-items:center;gap:18px;margin-top:4px;font-size:12px}
.contact-row svg{flex:none}
.bottom{left:0;top:2244px;width:1200px;height:38px;background:#111;border-top:2px solid var(--green)}
.bottom-links{left:162px;top:2256px;font-size:11px;color:#ddd}
.bottom-links a{color:#ddd;text-decoration:none}
.bottom-links a.active{color:var(--green)}
.copy{right:160px;top:2256px;font-size:11px;color:#ddd}
.copy b{color:var(--white)}
</style>
</head>
<body>
<div class="abs topline"></div>
<header class="abs header"></header>
<div class="abs brand"><div class="brand-mark">Bramblewood<br>Joinery</div></div>
<div class="abs social-badge"><span class="sq"></span>Social</div>
<div class="abs question">Have a Question for Us?</div>
<div class="abs phone">555 010 7890</div>

<div class="abs band"></div>
<nav class="abs nav">
  <a class="active">Home</a><a>Who we are</a><a>Getting started</a><a>Contact us</a><a>Customer experience</a><a>Professional</a><a>Portfolio</a><a>Cabinet hardware</a>
  <span class="search"><svg width="18" height="18" viewBox="0 0 18 18"><circle cx="7.5" cy="7.5" r="5.5" fill="none" stroke="#fff" stroke-width="2.2"/><line x1="11.5" y1="11.5" x2="16" y2="16" stroke="#fff" stroke-width="2.5"/></svg></span>
</nav>
<div class="abs slider" role="img" aria-label="Photo of a finished wooden kitchen with a central island"></div>
<div class="abs slide-arrow" style="left:174px"><svg width="16" height="18" viewBox="0 0 16 18"><polyline points="11,2 4,9 11,16" fill="none" stroke="#fff" stroke-width="3"/></svg></div>
<div class="abs slide-arrow" style="left:980px"><svg width="16" height="18" viewBox="0 0 16 18"><polyline points="5,2 12,9 5,16" fill="none" stroke="#fff" stroke-width="3"/></svg></div>
<div class="abs slide-title">AFFORDABLE SOLUTIONS FOR LIVING</div>
<div class="abs slide-sub">Style, Comfort, Quality, Selection!</div>
<div class="abs dots"><i></i><i></i><i class="on"></i><i></i><i></i></div>

<p class="abs intro">We’ve been <em>designing and manufacturing</em><br>the Midwest’s finest <em>custom cabinets and fixtures</em> since <em>1966</em></p>

<section class="abs offer"></section>
<h2 class="abs section-title" style="left:0;top:768px;width:1200px;text-align:center;color:#fff">What we offer</h2>
<div class="abs offer-item" style="left:153px"><svg width="60" height="50" viewBox="0 0 60 50"><circle cx="30" cy="25" r="16" fill="none" stroke="#bbb" stroke-width="3"/><circle cx="30" cy="25" r="10" fill="none" stroke="#bbb" stroke-width="2"/><line x1="6" y1="10" x2="6" y2="42" stroke="#bbb" stroke-width="3"/><line x1="54" y1="10" x2="54" y2="42" stroke="#bbb" stroke-width="3"/></svg>Kitchen</div>
<div class="abs offer-item on" style="left:268px"><svg width="60" height="50" viewBox="0 0 60 50"><path d="M8 24h44v8a10 10 0 0 1-10 10H18A10 10 0 0 1 8 32z" fill="none" stroke="#3db33d" stroke-width="3"/><path d="M14 24V10a5 5 0 0 1 10 0" fill="none" stroke="#3db33d" stroke-width="3"/><line x1="18" y1="42" x2="16" y2="48" stroke="#3db33d" stroke-width="3"/><line x1="42" y1="42" x2="44" y2="48" stroke="#3db33d" stroke-width="3"/></svg>Bath</div>
<div class="abs offer-item" style="left:378px"><svg width="60" height="50" viewBox="0 0 60 50"><rect x="8" y="26" width="44" height="4" fill="#bbb"/><rect x="12" y="30" width="3" height="16" fill="#bbb"/><rect x="45" y="30" width="3" height="16" fill="#bbb"/><rect x="22" y="8" width="18" height="14" fill="#bbb"/><circle cx="44" cy="12" r="5" fill="#bbb"/></svg>Office</div>
<div class="abs offer-item" style="left:520px"><svg width="60" height="50" viewBox="0 0 60 50"><path d="M24 4h12l-2 12 12 30H14l12-30z" fill="#bbb"/></svg>Closet/Dressing</div>
<div class="abs offer-item" style="left:703px"><svg width="60" height="50" viewBox="0 0 60 50"><rect x="8" y="22" width="44" height="5" fill="#bbb"/><rect x="12" y="27" width="3" height="18" fill="#bbb"/><rect x="45" y="27" width="3" height="18" fill="#bbb"/><circle cx="30" cy="12" r="8" fill="none" stroke="#bbb" stroke-width="3"/></svg>Workshop</div>
<div class="abs offer-item" style="left:870px"><svg width="60" height="50" viewBox="0 0 60 50"><rect x="6" y="20" width="48" height="24" fill="#bbb"/><circle cx="20" cy="10" r="6" fill="#bbb"/><circle cx="40" cy="10" r="6" fill="#bbb"/></svg>Entertainment</div>
<p class="abs offer-text">Sed ut perspiciatis unde omnis iste natus error sit voluptatem accusantium doloremque laudantium, totam rem aperiam, eaque ipsa quae ab illo inventore veritatis et quasi architecto beatae vitae dicta sunt explicabo. Nemo sit voluptatem doloremque laudantium, totam ratione voluptatem sequi nesciunt.</p>

<h2 class="abs section-title" style="left:162px;top:1076px">Our gallery</h2>
<div class="abs thumb light" style="left:162px;top:1118px;width:188px;height:99px" role="img" aria-label="White kitchen cabinetry"></div>
<div class="abs thumb light" style="left:363px;top:1118px;width:192px;height:99px" role="img" aria-label="Kitchen with stainless appliances"></div>
<div class="abs thumb" style="left:569px;top:1118px;width:192px;height:99px" role="img" aria-label="Living room media cabinet"></div>
<div class="abs thumb light" style="left:162px;top:1232px;width:188px;height:103px" role="img" aria-label="Open kitchen with dark island"></div>
<div class="abs thumb dark" style="left:363px;top:1232px;width:192px;height:103px" role="img" aria-label="Dark wood kitchen island"></div>
<div class="abs thumb dark" style="left:569px;top:1232px;width:192px;height:103px" role="img" aria-label="Espresso finish island"></div>
<div class="abs btn dark" style="left:162px;top:1350px;width:127px">View more</div>

<h2 class="abs section-title" style="left:787px;top:1076px">Recent news</h2>
<div class="abs news-item" style="top:1122px"><div class="nt thumb" role="img" aria-label="News thumbnail"></div><div><h4 class="hot">Morbi id malesuada augu elis</h4><p>Morbi id malesuada augue,auctor ahfc nunc sit amet, porttitor lobortis .</p></div></div>
<div class="abs news-item" style="top:1204px"><div class="nt thumb" role="img" aria-label="News thumbnail"></div><div><h4>Morbi id malesuada augu elis</h4><p>Morbi id malesuada augue,auctor ahfc nunc sit amet, porttitor lobortis .</p></div></div>
<div class="abs news-item" style="top:1288px"><div class="nt thumb" role="img" aria-label="News thumbnail"></div><div><h4>Morbi id malesuada augu elis</h4><p>Morbi id malesuada augue,auctor ahfc nunc sit amet, porttitor lobortis .</p></div></div>
<div class="abs btn green" style="left:787px;top:1350px;width:132px">View more</div>

<div class="abs rule"></div>

<h2 class="abs section-title" style="left:162px;top:1468px">Testimonials</h2>
<div class="abs avatar" role="img" aria-label="Portrait of the customer"></div>
<div class="abs bubble">“Lorem ipsum dolor sit amet, consectetur adipiscing elit, sed do eiusmod tempor incididunt ut labore et dolore magna aliqua. Ut enim ad minim veniam, quis nostrud exercitation ullamco laboris nisi ut aliquip ex ea commodo consequat. Duis aute irure dolor in reprehenderit in voluptate velit esse cillum dolore eu fugiat nulla. Excepteur sint cupidata”.</div>
<div class="abs quote-by">- Anna Rowe</div>

<h2 class="abs section-title" style="left:603px;top:1468px">Our clients</h2>
<div class="abs client" style="left:600px;top:1520px">Solene</div>
<div class="abs client" style="left:745px;top:1520px">Le Marais</div>
<div class="abs client" style="left:900px;top:1520px">Kestrel</div>
<div class="abs client" style="left:600px;top:1600px">Kestrel</div>
<div class="abs client" style="left:745px;top:1600px">Norvik</div>
<div class="abs client" style="left:900px;top:1600px">Halden</div>

<section class="abs hello"></section>
<h2 class="abs hello-title">HELLO !</h2>
<p class="abs hello-text">Sed ut perspiciatis unde omnis iste natus error sit voluptatem accusantium doloremque laudantium, totam rem aperiam, eaque ipsa quae e natus error sit voluptab illo inventore veritatis et quasi architecto beatae vitae dicta sunt explicabo.</p>
<div class="abs socials">
  <span style="background:#2a9fd8">Chirp</span>
  <span style="background:#3b5a9a">Social</span>
  <span style="background:#d34836">Plus</span>
  <span style="background:#1f8a3c"><svg width="18" height="18" viewBox="0 0 18 18"><circle cx="13" cy="4" r="2.5" fill="#fff"/><circle cx="4" cy="9" r="2.5" fill="#fff"/><circle cx="13" cy="14" r="2.5" fill="#fff"/><path d="M13 4L4 9l9 5" fill="none" stroke="#fff" stroke-width="1.5"/></svg></span>
</div>

<footer class="abs footer"></footer>
<h3 class="abs footer-title" style="left:162px">About us</h3>
<p class="abs footer-about">Established in <b>1966</b>, <b>Bramblewood Joinery</b> has long stood as one of the Midwest’s most renowned makers of custom cabinets and fixtures. Our handcrafted, award-winning creations have been chosen by hundreds of noteworthy homebuilders. And while we custom build cabinets, we built our business around the belief that our customers absolutely, unequivocally come first.</p>

<h3 class="abs footer-title" style="left:504px">Recent portfolio</h3>
<div class="abs pf thumb" style="left:504px;top:2045px" role="img" aria-label="Portfolio project"></div>
<div class="abs pf thumb light" style="left:566px;top:2045px" role="img" aria-label="Portfolio project"></div>
<div class="abs pf thumb dark" style="left:628px;top:2045px" role="img" aria-label="Portfolio project"></div>
<div class="abs pf thumb" style="left:690px;top:2045px" role="img" aria-label="Portfolio project"></div>
<div class="abs pf thumb light" style="left:504px;top:2097px" role="img" aria-label="Portfolio project"></div>
<div class="abs pf thumb dark" style="left:566px;top:2097px" role="img" aria-label="Portfolio project"></div>
<div class="abs pf thumb" style="left:628px;top:2097px" role="img" aria-label="Portfolio project"></div>
<div class="abs pf thumb light" style="left:690px;top:2097px" role="img" aria-label="Portfolio project"></div>
<div class="abs pf thumb dark" style="left:504px;top:2149px" role="img" aria-label="Portfolio project"></div>
<div class="abs pf thumb" style="left:566px;top:2149px" role="img" aria-label="Portfolio project"></div>
<div class="abs pf thumb light" style="left:628px;top:2149px" role="img" aria-label="Portfolio project"></div>
<div class="abs pf thumb dark" style="left:690px;top:2149px" role="img" aria-label="Portfolio project"></div>

<h3 class="abs footer-title" style="left:789px">Contact us</h3>
<div class="abs contact">
  <b>Got a question for Bramblewood? We’d love to hear from you! Whether it’s for a project inquiry.</b><br>
  <b>Bramblewood Joinery</b><br>
  Tom Hale, 200 Oak Lane, Fairview, MO-64000
  <div class="contact-row" style="margin-top:8px"><svg width="14" height="14" viewBox="0 0 14 14"><path d="M3 1l2 3-1.5 1.5a8 8 0 0 0 5 5L10 9l3 2-1.5 2.5A11 11 0 0 1 .5 2.5z" fill="#ddd"/></svg>: 555.010.2300</div>
  <div class="contact-row"><svg width="14" height="14" viewBox="0 0 14 14"><rect x="1" y="4" width="12" height="8" fill="#ddd"/><rect x="3" y="1" width="8" height="4" fill="#ddd"/></svg>: 555.010.7835</div>
  <div class="contact-row"><svg width="14" height="14" viewBox="0 0 14 14"><rect x="1" y="3" width="12" height="8" fill="#ddd"/><polyline points="1,3 7,8 13,3" fill="none" stroke="#2f2f2f" stroke-width="1.2"/></svg>: bill@bramblewoodjoinery.example</div>
</div>

<div class="abs bottom"></div>
<div class="abs bottom-links"><a class="active">Home</a> | <a>Who Are We</a> | <a>Professional</a> | <a>Portfolio</a> | <a>Contact Us</a></div>
<div class="abs copy">© 2015. All rights reserved. <b>Bramblewood Joinery.</b></div>
</body>
</html>
```